Redesign of business card for Cedar Ridge Mechanical

We are looking for a new design for our business cards for Cedar Ridge Mechanical. We are a plumbing & HVAC construction company, operating on the West Coast of Canada and USA. Logo attached.
Industry/Entity Type
Construction - Plumbing & HVAC
Contact Information for Business Card
Name, address, phone numbers, email, website address
Look and feel
Each slider illustrates characteristics of the customer's brand and the style your logo design should communicate.

```html
<!DOCTYPE html>
<html lang="en">
<head>
<meta charset="utf-8">
<title>Cedar Ridge Mechanical – Business Card</title>
<link href="https://fonts.googleapis.com/css2?family=Poppins:wght@300;400;600&display=swap" rel="stylesheet">
<style>
  :root {
    --stage: #262628;
    --card-rim: #ffffff;
    --card-face: #222225;
    --ink: #ffffff;
    --pattern-dark: #1c1c1f;
    --pattern-light: #3a3a3e;
  }
  * { box-sizing: border-box; margin: 0; padding: 0; }
  html, body { width: 1200px; height: 711px; overflow: hidden; }
  body {
    background: var(--stage);
    font-family: "Poppins", sans-serif;
    color: var(--ink);
    display: flex;
    align-items: center;
    justify-content: center;
    gap: 44px;
  }
  .card {
    position: relative;
    width: 540px;
    height: 310px;
    background: var(--card-rim);
    border-radius: 24px;
    padding: 13px;
    box-shadow: 0 14px 30px rgba(0,0,0,.55);
  }
  .card__face {
    position: relative;
    width: 100%;
    height: 100%;
    background: var(--card-face);
    border-radius: 14px;
    overflow: hidden;
  }
  .rim-break {
    position: absolute;
    width: 5px;
    height: 13px;
    background: var(--card-face);
  }
  .rim-break--tl { top: 0; left: 48px; }
  .rim-break--tr { top: 0; right: 48px; }
  .rim-break--bl { bottom: 0; left: 48px; }
  .rim-break--br { bottom: 0; right: 48px; }

  /* Back */
  .back__pattern {
    position: absolute;
    inset: 0;
    background: linear-gradient(200deg, var(--pattern-light) 0%, var(--pattern-dark) 60%);
  }
  .back__brand {
    position: absolute;
    right: 28px;
    bottom: 26px;
    display: flex;
    align-items: center;
    gap: 6px;
    font-size: 10px;
    font-weight: 400;
    letter-spacing: .5px;
  }
  .brand-square {
    width: 10px;
    height: 10px;
    border: 1.5px solid var(--ink);
  }

  /* Front */
  .front__brand {
    position: absolute;
    left: 26px;
    top: 98px;
    width: 200px;
    display: flex;
    align-items: center;
    gap: 12px;
    font-size: 19px;
    font-weight: 600;
    line-height: 1.15;
    text-transform: uppercase;
    letter-spacing: .5px;
  }
  .front__brand .brand-square {
    flex: none;
    width: 34px;
    height: 34px;
    border-width: 4px;
  }
  .front__divider {
    position: absolute;
    left: 250px;
    top: 48px;
    width: 1px;
    height: 150px;
    background: var(--ink);
  }
  .front__person {
    position: absolute;
    left: 278px;
    top: 58px;
  }
  .person__name { font-size: 24px; font-weight: 300; line-height: 1.1; }
  .person__name strong { font-weight: 600; }
  .person__role { font-size: 11px; font-weight: 400; margin-top: 2px; }
  .contact-list {
    list-style: none;
    margin-top: 20px;
    display: grid;
    gap: 5px;
  }
  .contact-list li {
    display: flex;
    align-items: center;
    gap: 9px;
    font-size: 12px;
    font-weight: 300;
  }
  .contact-list svg { width: 12px; height: 12px; flex: none; }
  .front__address {
    position: absolute;
    left: 0;
    right: 0;
    bottom: 30px;
    text-align: center;
    font-size: 12px;
    font-weight: 300;
  }
</style>
</head>
<body>

  <section class="card card--back">
    <div class="card__face">
      <div class="back__pattern" role="img" aria-label="Repeating brand mark pattern on dark background"></div>
      <div class="back__brand"><span class="brand-square"></span>Cedar Ridge Mechanical</div>
    </div>
    <span class="rim-break rim-break--tl"></span>
    <span class="rim-break rim-break--tr"></span>
    <span class="rim-break rim-break--bl"></span>
    <span class="rim-break rim-break--br"></span>
  </section>

  <section class="card card--front">
    <div class="card__face">
      <div class="front__brand"><span class="brand-square"></span>Cedar Ridge Mechanical</div>
      <div class="front__divider"></div>
      <div class="front__person">
        <h1 class="person__name"><strong>Marta</strong> Kovac</h1>
        <p class="person__role">Founder &amp; CEO</p>
        <ul class="contact-list">
          <li>
            <svg viewBox="0 0 24 24" fill="#fff"><path d="M6.6 10.8a15.1 15.1 0 0 0 6.6 6.6l2.2-2.2a1 1 0 0 1 1-.25 11.4 11.4 0 0 0 3.6.57 1 1 0 0 1 1 1V20a1 1 0 0 1-1 1A17 17 0 0 1 3 4a1 1 0 0 1 1-1h3.5a1 1 0 0 1 1 1c0 1.25.2 2.45.57 3.57a1 1 0 0 1-.25 1z"/></svg>
            (555) 214-0386
          </li>
          <li>
            <svg viewBox="0 0 24 24" fill="none" stroke="#fff" stroke-width="2"><rect x="3" y="5" width="18" height="14" rx="1"/><path d="M3 6l9 7 9-7"/></svg>
            info@cedarridgemech.com
          </li>
          <li>
            <svg viewBox="0 0 24 24" fill="none" stroke="#fff" stroke-width="2"><circle cx="12" cy="12" r="9"/><path d="M3 12h18M12 3c3 3.5 3 14.5 0 18M12 3c-3 3.5-3 14.5 0 18"/></svg>
            www.cedarridgemech.com
          </li>
        </ul>
      </div>
      <p class="front__address">418 Harbor Lane Suite 12 Portland, OR 97201</p>
    </div>
    <span class="rim-break rim-break--tl"></span>
    <span class="rim-break rim-break--tr"></span>
    <span class="rim-break rim-break--bl"></span>
    <span class="rim-break rim-break--br"></span>
  </section>

</body>
</html>
```